The quiet harbor with an elephant incorporated in the background

Target Market(s)

Real estate

Industry/Entity Type

Real Estate

Contact Information for Business Card

On back on want my name & number
In front I want the business name, "the quiet harbor", below to say staging & design

Logo Text

The quiet harbor

Font styles to use
Serif

Colors
000000

Requirements
Must have
• I want an elephant behind the writing in gold transperant

```html
<!DOCTYPE html>
<html lang="en">
<head>
<meta charset="utf-8">
<title>The Quiet Harbor – Business Cards</title>
<link href="https://fonts.googleapis.com/css2?family=Cinzel:wght@500&family=Open+Sans:wght@300;400&display=swap" rel="stylesheet">
<style>
  :root {
    --backdrop: #ececec;
    --card-black: #000000;
    --card-charcoal: #121212;
    --gold: #f4a70f;
    --elephant-tone: #2b2718;
    --elephant-tone-soft: #1d1b14;
    --text-light: #e8e8e8;
    --text-muted: #8a8a8a;
  }
  * { margin: 0; padding: 0; box-sizing: border-box; }
  html, body {
    width: 1200px;
    height: 900px;
    overflow: hidden;
    background: var(--backdrop);
  }
  .stage {
    position: relative;
    width: 1200px;
    height: 900px;
    display: flex;
    align-items: center;
    justify-content: center;
    gap: 60px;
  }
  .card {
    position: relative;
    width: 500px;
    height: 286px;
    overflow: hidden;
    box-shadow: 0 14px 30px rgba(0, 0, 0, 0.18);
  }
  .card--details { background: var(--card-charcoal); }
  .card--brand { background: var(--card-black); }

  .brand {
    position: absolute;
    display: flex;
    flex-direction: column;
    align-items: center;
  }
  .brand__row {
    display: flex;
    align-items: center;
    gap: 10px;
  }
  .brand__mark {
    width: 14px;
    height: 14px;
    background: var(--gold);
  }
  .brand__name {
    font-family: "Cinzel", serif;
    font-weight: 500;
    font-size: 25px;
    letter-spacing: 0.5px;
    color: var(--gold);
    white-space: nowrap;
  }
  .brand__tagline {
    margin-top: 2px;
    font-family: "Open Sans", sans-serif;
    font-weight: 300;
    font-size: 13px;
    letter-spacing: 0.5px;
    color: var(--text-muted);
  }
  .card--brand .brand {
    left: 0; right: 0; top: 112px;
  }

  .elephant-art {
    position: absolute;
    left: 40px;
    top: 48px;
    width: 330px;
    height: 190px;
    border-radius: 46% 52% 30% 34% / 48% 50% 30% 30%;
    background: radial-gradient(ellipse at 45% 40%, var(--elephant-tone) 0%, var(--elephant-tone-soft) 70%, transparent 100%);
  }
  .holder-name {
    position: absolute;
    left: 26px;
    top: 22px;
    font-family: "Cinzel", serif;
    font-weight: 500;
    font-size: 16px;
    color: var(--gold);
  }
  .contact-list {
    position: absolute;
    left: 26px;
    top: 108px;
    list-style: none;
    font-family: "Open Sans", sans-serif;
    font-size: 11px;
    color: var(--text-light);
    line-height: 17px;
  }
  .contact-list li {
    display: flex;
    align-items: center;
    gap: 6px;
  }
  .contact-list svg { width: 9px; height: 9px; fill: var(--gold); }
  .card--details .brand {
    right: 30px;
    top: 112px;
  }
  .address {
    position: absolute;
    right: 30px;
    bottom: 24px;
    font-family: "Open Sans", sans-serif;
    font-size: 11.5px;
    line-height: 17px;
    color: var(--text-light);
    text-align: right;
  }
</style>
</head>
<body>
<main class="stage">
  <section class="card card--details">
    <div class="elephant-art" role="img" aria-label="Faint gold elephant silhouette in the background"></div>
    <p class="holder-name">Daniel Reeves</p>
    <ul class="contact-list">
      <li>
        <svg viewBox="0 0 10 10" aria-hidden="true"><path d="M2 0.5 L3.6 0.5 L4.2 2.8 L3 3.6 Q4 5.8 6.4 7 L7.2 5.8 L9.5 6.4 L9.5 8 Q9.5 9.5 8 9.5 Q0.5 9 0.5 2 Q0.5 0.5 2 0.5 Z"/></svg>
        (044)987650321
      </li>
      <li>
        <svg viewBox="0 0 10 10" aria-hidden="true"><rect x="0.5" y="1.5" width="9" height="7" rx="1"/></svg>
        hello@quietharbor.com
      </li>
    </ul>
    <div class="brand">
      <div class="brand__row">
        <span class="brand__mark" aria-hidden="true"></span>
        <span class="brand__name">The Quiet Harbor</span>
      </div>
      <span class="brand__tagline">staging &amp; design</span>
    </div>
    <p class="address">5678, Harbor Lane,<br>Westfield, 54321</p>
  </section>

  <section class="card card--brand">
    <div class="brand">
      <div class="brand__row">
        <span class="brand__mark" aria-hidden="true"></span>
        <span class="brand__name">The Quiet Harbor</span>
      </div>
      <span class="brand__tagline">staging &amp; design</span>
    </div>
  </section>
</main>
</body>
</html>
```